Packaging sleeve for food containers

I have designed eco-friendly food prep containers that come in packs of 10. The food containers are beige with a clear lid. I need a design for a cardboard sleeve that wraps around the containers as part of the packaging with all of the information on it. I will upload a basic idea of what I am looking for as well as 2 other similar brands for comparison. I have a template with the information I require to be included but I need the final design to be jazzed up to a professional standard. I need help with colours and the design of the sleeve.

Target Market(s)

People who like to meal prep their food in advance and who might also be environmentally conscious. Female and male, somewhat health conscious. Might be looking to lose or maintain weight or just improve nutrition. Organised people. Age range 20-50(ish).

Font styles to use
Serif
Sans Serif

Requirements
Must have
• The information contained in my example sleeve
Nice to have
• Harmonious colours

```html
<!DOCTYPE html>
<html lang="en">
<head>
<meta charset="utf-8">
<title>Stack n Savour – Meal Prep Containers Sleeve</title>
<link href="https://fonts.googleapis.com/css2?family=Archivo+Black&family=Courier+Prime:wght@400;700&family=Open+Sans:wght@700&display=swap" rel="stylesheet">
<style>
  :root {
    --page: #e6ede3;
    --green: #157350;
    --yellow: #fbb021;
    --cream: #eef0e4;
    --white: #ffffff;
    --guide: #29a9d6;
    --ink: #222222;
    --wood-dark: #5a3422;
    --wood-mid: #8a5a3e;
    --wood-light: #a77458;
  }
  html, body { margin: 0; padding: 0; }
  body {
    width: 1200px; height: 3243px; overflow: hidden;
    background: var(--page); position: relative;
    font-family: "Courier Prime", monospace;
  }
  .dimension {
    position: absolute; font-family: Georgia, "Times New Roman", serif;
    font-size: 52px; color: var(--ink); line-height: 1;
  }
  .dimension--width { left: 360px; top: 55px; }
  .sleeve {
    position: absolute; left: 101px; top: 135px; width: 819px; height: 3019px;
    outline: 2px solid var(--guide);
  }
  .panel { position: absolute; left: 0; width: 819px; background: var(--green); border-bottom: 2px solid var(--guide); box-sizing: border-box; overflow: hidden; }
  .panel--top { top: 0; height: 608px; }
  .panel--front { top: 608px; height: 950px; }
  .panel--features { top: 1558px; height: 609px; }
  .panel--back { top: 2167px; height: 755px; }
  .panel--flap { top: 2922px; height: 97px; border-bottom: none; }

  /* top panel, printed upside down */
  .flipped { position: absolute; inset: 0; transform: rotate(180deg); }
  .line { position: absolute; left: 0; right: 0; text-align: center; color: var(--white); font-size: 31px; line-height: 1; transform: translateY(-50%); }
  .line--headline { font-family: "Archivo Black", sans-serif; color: var(--yellow); font-size: 36px; letter-spacing: 1px; }
  .inline-square { display: inline-block; width: 34px; height: 34px; background: var(--white); border-radius: 7px; vertical-align: middle; margin: 0 10px; }

  /* front */
  .photo { position: absolute; inset: 0;
    background: linear-gradient(100deg, var(--wood-dark) 0%, var(--wood-light) 45%, var(--wood-mid) 75%, #c9602e 100%); }
  .brand-seal { position: absolute; width: 398px; height: 398px; border: 4px solid var(--cream); border-radius: 50%; box-sizing: border-box;
    display: flex; align-items: center; justify-content: center; }
  .brand-seal--front { left: 20px; top: 17px; }
  .brand-name { font-family: "Archivo Black", sans-serif; color: var(--cream); font-size: 36px; letter-spacing: 4px; white-space: nowrap; }
  .pack-badge { position: absolute; left: 650px; top: 59px; width: 134px; height: 134px; border-radius: 50%; background: var(--white);
    border: 4px solid var(--green); box-sizing: border-box; display: flex; flex-direction: column; align-items: center; justify-content: center;
    font-family: "Open Sans", sans-serif; font-weight: 700; color: var(--green); font-size: 36px; line-height: 1.05; }
  .product-title { position: absolute; left: 32px; font-family: "Archivo Black", sans-serif; line-height: 1; white-space: nowrap; }
  .product-title--meal { top: 457px; color: var(--yellow); font-size: 72px; letter-spacing: 6px; }
  .product-title--containers { top: 530px; color: var(--white); font-size: 70px; letter-spacing: 2px; }
  .product-sub { position: absolute; left: 40px; top: 620px; color: var(--white); font-family: "Archivo Black", sans-serif; font-size: 42px; letter-spacing: 2px; }
  .eco-band { position: absolute; left: 0; top: 700px; width: 819px; height: 85px; background: var(--yellow);
    display: flex; align-items: center; justify-content: center; gap: 24px; font-family: "Archivo Black", sans-serif; font-size: 48px; letter-spacing: 4px; }
  .eco-band .eco { color: var(--green); }
  .eco-band .material { color: var(--white); }
  .compartment-icon { position: absolute; left: 63px; top: 833px; }

  /* features */
  .feature-box { position: absolute; left: 157px; top: 80px; width: 497px; height: 468px; border: 5px solid var(--yellow); box-sizing: border-box; }
  .feature { position: absolute; width: 150px; margin-left: -75px; text-align: center; }
  .feature svg { display: block; margin: 0 auto; }
  .feature-label { font-family: "Open Sans", sans-serif; font-weight: 700; font-size: 13px; color: var(--yellow); line-height: 1; margin-top: 4px; }

  /* back */
  .brand-seal--back { left: 256px; top: 199px; width: 328px; height: 328px; border-color: var(--white); }
  .brand-seal--back .brand-name { color: var(--white); font-size: 28px; letter-spacing: 3px; }
  .web-band { position: absolute; left: 0; top: 620px; width: 819px; height: 63px; background: var(--yellow);
    display: flex; align-items: center; justify-content: center; color: var(--white); font-family: "Archivo Black", sans-serif; font-size: 32px; letter-spacing: 3px; }
</style>
</head>
<body>
  <div class="dimension dimension--width">168mm</div>
  <div class="dimension" style="left:934px;top:402px">125mm</div>
  <div class="dimension" style="left:934px;top:1198px">195mm</div>
  <div class="dimension" style="left:934px;top:1947px">125mm</div>
  <div class="dimension" style="left:934px;top:2709px">155mm</div>
  <div class="dimension" style="left:934px;top:3093px">20mm</div>

  <div class="sleeve">
    <section class="panel panel--top">
      <div class="flipped">
        <div class="line line--headline" style="top:155px">Winner Winner Meal Prep dinner!</div>
        <div class="line" style="top:218px">Tag us @StacknSavour on <span class="inline-square"></span> with</div>
        <div class="line" style="top:278px">your containers to win monthly prizes</div>
        <div class="line" style="top:377px">Connect with us</div>
        <div class="line" style="top:437px">www.stacknsavour.com.au</div>
        <div class="line" style="top:496px">@StacknSavour</div>
      </div>
    </section>

    <section class="panel panel--front">
      <div class="photo" role="img" aria-label="Photograph of a wooden table with capsicums, tomatoes, eggplant, olives, peppercorns and dry spaghetti"></div>
      <div class="brand-seal brand-seal--front"><span class="brand-name">Stack n Savour</span></div>
      <div class="pack-badge"><span>10</span><span>Pack</span></div>
      <div class="product-title product-title--meal">Meal Prep</div>
      <div class="product-title product-title--containers">CONTAINERS</div>
      <div class="product-sub">3 compartment</div>
      <div class="eco-band"><span class="eco">Eco Friendly</span><span class="material">Wheatstraw</span></div>
      <svg class="compartment-icon" width="146" height="93" viewBox="0 0 146 93">
        <rect x="1.5" y="1.5" width="143" height="90" fill="var(--yellow)" stroke="var(--white)" stroke-width="3"/>
        <rect x="14" y="10" width="54" height="73" rx="12" fill="none" stroke="var(--white)" stroke-width="3"/>
        <rect x="76" y="10" width="56" height="34" rx="12" fill="none" stroke="var(--white)" stroke-width="3"/>
        <rect x="76" y="49" width="56" height="34" rx="12" fill="none" stroke="var(--white)" stroke-width="3"/>
        <g font-family="Archivo Black, sans-serif" font-size="22" fill="var(--white)" text-anchor="middle">
          <text x="41" y="54">2c</text><text x="104" y="35">1c</text><text x="104" y="74">1c</text>
        </g>
      </svg>
    </section>

    <section class="panel panel--features">
      <div class="feature-box">
        <div class="feature" style="left:128px;top:35px">
          <svg width="96" height="96" viewBox="0 0 96 96" fill="none" stroke="var(--yellow)" stroke-width="4">
            <circle cx="48" cy="48" r="44"/><rect x="22" y="30" width="52" height="36" rx="4"/><rect x="28" y="36" width="30" height="24"/><circle cx="66" cy="42" r="2.5"/>
          </svg>
          <div class="feature-label">Microwave<br>Safe</div>
        </div>
        <div class="feature" style="left:256px;top:35px">
          <svg width="96" height="96" viewBox="0 0 96 96" fill="none" stroke="var(--yellow)" stroke-width="4">
            <circle cx="48" cy="48" r="44"/><path d="M48 22v52M25 35l46 26M25 61l46-26"/>
          </svg>
          <div class="feature-label">Freezer<br>Safe</div>
        </div>
        <div class="feature" style="left:383px;top:35px">
          <svg width="96" height="96" viewBox="0 0 96 96" fill="none" stroke="var(--yellow)" stroke-width="4">
            <circle cx="48" cy="48" r="44"/><circle cx="45" cy="58" r="14"/><circle cx="60" cy="58" r="12"/><path d="M22 40l20-20M28 44l22-22M34 46l24-24"/>
          </svg>
          <div class="feature-label">Dishwasher<br>Safe</div>
        </div>
        <div class="feature" style="left:121px;top:180px">
          <svg width="96" height="96" viewBox="0 0 96 96" fill="none" stroke="var(--yellow)" stroke-width="4">
            <circle cx="48" cy="48" r="44"/>
            <text x="44" y="46" font-family="Open Sans, sans-serif" font-weight="700" font-size="22" fill="var(--yellow)" stroke="none" text-anchor="middle">BPA</text>
            <text x="44" y="68" font-family="Open Sans, sans-serif" font-weight="700" font-size="20" fill="var(--yellow)" stroke="none" text-anchor="middle">FREE</text>
          </svg>
          <div class="feature-label">BPA Free</div>
        </div>
        <div class="feature" style="left:256px;top:180px">
          <svg width="96" height="96" viewBox="0 0 96 96" fill="none" stroke="var(--yellow)" stroke-width="4">
            <circle cx="48" cy="48" r="44"/><path d="M48 76V28M48 44l-10-8M48 44l10-8M48 56l-10-8M48 56l10-8M48 32l-6-8M48 32l6-8"/>
          </svg>
          <div class="feature-label">Wheatstraw</div>
        </div>
        <div class="feature" style="left:383px;top:180px">
          <svg width="96" height="96" viewBox="0 0 96 96" fill="none" stroke="var(--yellow)" stroke-width="4">
            <circle cx="48" cy="48" r="44"/><path d="M48 22c-10 16-18 26-18 36a18 18 0 0 0 36 0c0-10-8-20-18-36z"/><path d="M22 22l52 52"/>
          </svg>
          <div class="feature-label">Leakproof</div>
        </div>
        <div class="feature" style="left:121px;top:325px">
          <svg width="96" height="96" viewBox="0 0 96 96" fill="none" stroke="var(--yellow)" stroke-width="4">
            <circle cx="48" cy="48" r="44"/><rect x="18" y="34" width="60" height="9" rx="3"/><rect x="18" y="46" width="60" height="9" rx="3"/><rect x="18" y="58" width="60" height="9" rx="3"/>
          </svg>
          <div class="feature-label">Stackable</div>
        </div>
        <div class="feature" style="left:256px;top:325px">
          <svg width="96" height="96" viewBox="0 0 96 96" fill="none" stroke="var(--yellow)" stroke-width="4">
            <circle cx="48" cy="48" r="44"/><circle cx="30" cy="38" r="8"/><circle cx="48" cy="38" r="8"/><circle cx="66" cy="38" r="8"/><circle cx="30" cy="60" r="8"/><circle cx="48" cy="60" r="8"/><circle cx="66" cy="60" r="8"/>
          </svg>
          <div class="feature-label">Reusable</div>
        </div>
        <div class="feature" style="left:388px;top:325px">
          <svg width="96" height="96" viewBox="0 0 96 96" fill="none" stroke="var(--yellow)" stroke-width="4">
            <circle cx="48" cy="48" r="44"/><path d="M48 24l20 34H28z"/><path d="M62 48l6 10-11 1"/>
          </svg>
          <div class="feature-label">Recycle</div>
        </div>
      </div>
    </section>

    <section class="panel panel--back">
      <div class="brand-seal brand-seal--back"><span class="brand-name">Stack n Savour</span></div>
      <div class="web-band">www.stacknsavour.com.au</div>
    </section>

    <section class="panel panel--flap"></section>
  </div>
</body>
</html>
```